Oil Field Service company needs professional business cards

Looking to clean up our current company business cards and look a little more professional. Brenwick Casing Services is a US based company that services the oil field. We deal with engineers, managers and oil rigs....................................................................................................................................................................................................................................................................................................................................................................................................

Target Market(s)

Oil and Gas professionals

Industry/Entity Type

Oil And Gas

Contact Information for Business Card

See attached photo as example

Font styles to use
Sans Serif

Colors
ec1f27

Requirements
Must have
• Company Logo, Name, Title, Cell, Office, Fax, Email.
• See attached photo
Nice to have
• External CRT, Internal CRT, Casing Crews, Torque Turn, Laydown Machine
Should not have
• Do not introduce any new pictures and keep it professional looking

```html
<!DOCTYPE html>
<html lang="en">
<head>
<meta charset="utf-8">
<title>Brenwick Casing Services – Business Cards</title>
<link href="https://fonts.googleapis.com/css2?family=Open+Sans:wght@400;600;700&display=swap" rel="stylesheet">
<style>
  :root {
    --backdrop: #3b3531;
    --card: #0f0f10;
    --card-edge: #1c1c1e;
    --brand-red: #ec1f27;
    --brand-grey: #5d6770;
    --text-light: #f2f2f2;
    --divider: #5a1417;
  }
  * { box-sizing: border-box; margin: 0; padding: 0; }
  html, body {
    width: 1200px; height: 900px; overflow: hidden;
    background: var(--backdrop);
    font-family: "Open Sans", Arial, sans-serif;
  }
  .canvas {
    position: relative; width: 1200px; height: 900px;
    display: flex; align-items: center; justify-content: center; gap: 50px;
  }
  .card {
    position: relative; width: 540px; height: 310px;
    background: var(--card);
    border: 1px solid var(--card-edge);
    border-radius: 3px;
    box-shadow: 0 10px 24px rgba(0,0,0,.45);
  }
  .brand-name {
    color: var(--brand-grey);
    font-weight: 700;
    text-transform: uppercase;
    line-height: 1.05;
  }
  .brand-name .brand-main { display: block; letter-spacing: 3px; }
  .brand-name .brand-sub { display: block; letter-spacing: 3px; }

  /* Contact side */
  .card-front .brand-name {
    position: absolute; left: 34px; top: 110px; width: 220px;
  }
  .card-front .brand-main { font-size: 36px; }
  .card-front .brand-sub { font-size: 12.5px; margin-top: 6px; letter-spacing: 4px; }
  .divider {
    position: absolute; left: 268px; top: 70px; width: 1px; height: 140px;
    background: var(--divider);
  }
  .contact { position: absolute; left: 290px; top: 64px; color: var(--text-light); }
  .contact-name { color: var(--brand-red); font-weight: 700; font-size: 16px; }
  .contact-title { font-size: 12px; margin-bottom: 14px; }
  .contact-list { list-style: none; font-size: 13px; line-height: 19px; }
  .contact-list li { display: flex; align-items: center; gap: 9px; }
  .contact-list svg { width: 10px; height: 10px; fill: var(--brand-red); flex: none; }
  .services {
    position: absolute; left: 34px; bottom: 26px;
    color: var(--text-light); font-size: 15px;
  }
  .services .sep { margin: 0 4px; }

  /* Logo side */
  .card-back { display: flex; align-items: center; justify-content: center; }
  .card-back .brand-name { text-align: center; }
  .card-back .brand-main { font-size: 44px; }
  .card-back .brand-sub { font-size: 14px; margin-top: 8px; letter-spacing: 5px; }
</style>
</head>
<body>
<main class="canvas">
  <section class="card card-front">
    <p class="brand-name"><span class="brand-main">Brenwick</span><span class="brand-sub">Casing Services</span></p>
    <div class="divider"></div>
    <div class="contact">
      <p class="contact-name">Cody Harlan</p>
      <p class="contact-title">Area Manager</p>
      <ul class="contact-list">
        <li><svg viewBox="0 0 10 10" aria-label="Office"><path d="M2 0.5 L3.6 2.4 L2.7 3.6 Q3.8 5.9 6.2 7.2 L7.4 6.3 L9.5 7.9 L8.3 9.5 Q2.6 8.6 0.5 1.7 Z"/></svg>(555) 214-0381</li>
        <li><svg viewBox="0 0 10 10" aria-label="Cell"><path d="M2.5 0 H7.5 V10 H2.5 Z M3.4 1.2 V7.8 H6.6 V1.2 Z"/></svg>(555) 309-7724</li>
        <li><svg viewBox="0 0 10 10" aria-label="Fax"><path d="M2.5 0 H7 V3 H2.5 Z M0.5 3.5 H9.5 V9.5 H0.5 Z"/></svg>(555) 214-0399</li>
        <li><svg viewBox="0 0 10 10" aria-label="Email"><path d="M0.5 2 H9.5 V8.5 H0.5 Z M1.2 2.7 L5 5.6 L8.8 2.7" stroke="#0f0f10" stroke-width="0.8"/></svg>cody.harlan@brenwickmail.com</li>
      </ul>
    </div>
    <p class="services">Laydown Machine<span class="sep">|</span>Casing Crew<span class="sep">|</span>Mud Tool<span class="sep">|</span>Torque Turn</p>
  </section>

  <section class="card card-back">
    <p class="brand-name"><span class="brand-main">Brenwick</span><span class="brand-sub">Casing Services</span></p>
  </section>
</main>
</body>
</html>
```